Dental office stationary (letterhead, envelopes), business cards, presentation folders

Nothing too dental outside of the logo. I will need all stationary, presentation folders, business cards. Would prefer to stay in the colors of the logo

Gordon Patel, DDS
Bright Haven Dental Implant Center
555-318-2790
info@brighthavendental.example
4817 NW Maple Crest Rd Unit B
Harborview, ST 00000

Also need appointment date and time
And cancellation policy
I want it to say “kindly ask for
A 48hr cancellation policy to avoid incurring a cancellation fee”

Industry/Entity Type

Dental

Colors
0054AA
0677BA
7BADD7
CADEEF
E8F1F8

Requirements
Must have
• Name of your office, name of doctor, address, phone number
Should not have
• Too much tooth/dental. Only the tooth in logo

```html
<!DOCTYPE html>
<html lang="en">
<head>
<meta charset="utf-8">
<title>Bright Haven Dental Implant Center — Stationery Set</title>
<link href="https://fonts.googleapis.com/css2?family=Roboto:wght@300;400;700&display=swap" rel="stylesheet">
<style>
  :root{
    --bg:#c9c9c9;
    --sky:#17c2f0;
    --blue:#0d6cbe;
    --deep:#0c5fae;
    --teal:#1dba94;
    --ink:#3b3b3b;
    --paper:#ffffff;
    --mist:#e6e8ea;
    --shadow:0 2px 5px rgba(0,0,0,.28);
  }
  *{box-sizing:border-box;margin:0;padding:0}
  html,body{width:1200px;height:1011px;overflow:hidden}
  body{background:var(--bg);font-family:'Roboto',Arial,sans-serif;color:var(--ink);position:relative}
  .piece{position:absolute;background:var(--paper);box-shadow:var(--shadow);overflow:hidden}
  .piece svg.shape{position:absolute;left:0;top:0}
  .grad-band{background:linear-gradient(90deg,var(--sky),var(--blue))}

  /* wordmark */
  .mark{position:absolute;text-align:center;font-family:'Roboto',Arial,sans-serif;font-weight:400;color:var(--blue);line-height:1}
  .mark-name{display:block;letter-spacing:.04em;text-transform:uppercase;white-space:nowrap}
  .mark-sub{display:block;letter-spacing:.32em;text-transform:uppercase;margin-top:2px;white-space:nowrap}
  .mark.light{color:#fff}

  /* business card */
  .card{left:53px;top:99px;width:325px;height:185px}
  .card-info{position:absolute;left:16px;top:34px;color:#fff;font-size:8.6px;line-height:1.3}
  .card-name{font-weight:700;font-size:10.6px}
  .card-block{margin-top:18px}
  .card-contact{margin-top:20px}
  .card-contact li{list-style:none;display:flex;align-items:center;gap:3px}
  .ico{width:7px;height:7px;fill:#fff;flex:none}

  /* appointment card */
  .appt{left:53px;top:315px;width:325px;height:185px}
  .appt-head{position:absolute;left:0;top:0;width:100%;height:66px}
  .appt-line{position:absolute;left:0;top:68px;width:100%;height:2px;background:var(--teal)}
  .appt-tab{position:absolute;left:0;top:70px}
  .appt-tab-label{position:absolute;left:0;top:70px;width:100%;text-align:center;color:#fff;font-size:11.5px;line-height:14px}
  .appt-dash{position:absolute;left:21px;right:21px;top:109px;border-top:1px dashed #aaa}
  .appt-row{position:absolute;left:21px;right:21px;top:127px;display:flex;align-items:flex-end;font-size:9px;gap:2px}
  .appt-row .blank{flex:1;border-bottom:1px solid #777;height:8px;margin-right:3px}
  .appt-note{position:absolute;left:0;width:100%;top:151px;text-align:center;font-size:8.3px;line-height:1.3}

  /* letter */
  .letter{left:402px;top:97px;width:285px;height:403px}
  .head-contact{position:absolute;color:#fff;font-size:4.4px;line-height:1.25;white-space:nowrap}
  .head-contact .gap{height:4px}
  .letter-body{position:absolute;left:26px;right:26px;font-size:4.4px;line-height:1.3;color:#555}
  .letter-body .greet{font-size:6.4px;color:#333;margin-bottom:12px}
  .letter-body p{margin-bottom:6px}
  .letter-body .sign-off{font-size:3.8px;margin-top:10px}
  .signature{width:36px;height:12px;margin-top:10px;background:linear-gradient(90deg,#9a9a9a,#cfcfcf);border-radius:3px;opacity:.5}

  /* envelopes */
  .env-back{left:715px;top:99px;width:431px;height:187px}
  .env-addr{position:absolute;left:15px;top:26px;color:#fff;font-size:6.4px;line-height:1.3}
  .env-flap{left:713px;top:312px;width:434px;height:189px}

  /* folders */
  .folder-closed{left:56px;top:540px;width:527px;height:373px}
  .folder-cover{position:absolute;left:0;top:0;width:264px;height:100%}
  .folder-inner{position:absolute;left:264px;top:0;width:263px;height:100%;background:linear-gradient(90deg,#e4e6e8,#ffffff 70%)}
  .folder-open{left:625px;top:538px;width:524px;height:376px;background:transparent}
  .open-left{position:absolute;left:0;top:0;width:262px;height:100%;background:linear-gradient(90deg,#ffffff,#ebedee)}
  .open-right{position:absolute;left:262px;top:0;width:262px;height:100%;background:linear-gradient(90deg,#c3c5c8,#e9eaec 60%,#f4f4f4)}
  .inset-letter{position:absolute;left:276px;top:17px;width:248px;height:230px;background:#fafafa}
</style>
</head>
<body>

<section class="piece card">
  <svg class="shape" width="325" height="185" viewBox="0 0 325 185">
    <defs>
      <linearGradient id="cardGrad" x1="0" x2="1" y1="0" y2="0">
        <stop offset="0" stop-color="#17c2f0"/><stop offset="1" stop-color="#0c5fae"/>
      </linearGradient>
    </defs>
    <path d="M0 0H206Q138 92 206 185H0Z" fill="url(#cardGrad)"/>
    <path d="M206 0Q138 92 206 185" fill="none" stroke="#1dba94" stroke-width="2"/>
  </svg>
  <div class="card-info">
    <div class="card-name">Gordon Patel, DDS</div>
    <div>Bright Haven Dental Implant Center</div>
    <div class="card-block">4817 NW Maple Crest Rd Unit B<br>Harborview, ST 00000</div>
    <ul class="card-contact">
      <li><svg class="ico" viewBox="0 0 10 10"><path d="M2 1l2 2-1 1.5c.6 1.2 1.3 1.9 2.5 2.5L7 6l2 2-1.2 1.5C4 9 1 6 .5 2.2z"/></svg>555-318-2790</li>
      <li><svg class="ico" viewBox="0 0 10 10"><path d="M0 2h10v6H0z"/><path d="M0 2l5 3.5L10 2" fill="none" stroke="#0d6cbe" stroke-width=".8"/></svg>info@brighthavendental.example</li>
      <li><svg class="ico" viewBox="0 0 10 10"><circle cx="5" cy="5" r="4.5"/></svg>www.brighthavendental.example</li>
    </ul>
  </div>
  <div class="mark" style="left:210px;top:88px;width:112px">
    <span class="mark-name" style="font-size:15px">Bright Haven</span>
    <span class="mark-sub" style="font-size:4.6px;letter-spacing:.26em">Dental Implant Center</span>
  </div>
</section>

<section class="piece appt">
  <div class="appt-head grad-band"></div>
  <div class="mark light" style="left:0;top:28px;width:325px">
    <span class="mark-name" style="font-size:20px">Bright Haven</span>
    <span class="mark-sub" style="font-size:6px">Dental Implant Center</span>
  </div>
  <div class="appt-line"></div>
  <svg class="appt-tab" width="325" height="14" viewBox="0 0 325 14"><path d="M84 0H241L228 14H97Z" fill="#1dba94"/></svg>
  <div class="appt-tab-label">APPOINTMENT</div>
  <div class="appt-dash"></div>
  <div class="appt-row">DATE :<span class="blank"></span>TIME :<span class="blank" style="flex:.75"></span></div>
  <p class="appt-note">If you are unable to keep this appointment please notify us at least<br><b>48 hours</b> in advance to avoid a broken appointment charge</p>
</section>

<section class="piece letter">
  <svg class="shape" width="285" height="60" viewBox="0 0 285 60">
    <defs><linearGradient id="lhGrad" x1="0" x2="1"><stop offset="0" stop-color="#17c2f0"/><stop offset="1" stop-color="#0c5fae"/></linearGradient></defs>
    <path d="M0 11H200Q183 32 200 54H0Z" fill="url(#lhGrad)"/>
    <path d="M200 11Q183 32 200 54" fill="none" stroke="#1dba94" stroke-width="1"/>
  </svg>
  <div class="head-contact" style="left:15px;top:17px">4817 NW Maple Crest Rd Unit B<br>Harborview, ST 00000<div class="gap"></div>&#9743; 555-318-2790<br>&#9993; info@brighthavendental.example<br>&#9679; www.brighthavendental.example</div>
  <div class="mark" style="left:196px;top:27px;width:86px">
    <span class="mark-name" style="font-size:11.5px">Bright Haven</span>
    <span class="mark-sub" style="font-size:3.4px;letter-spacing:.24em">Dental Implant Center</span>
  </div>
  <div class="letter-body" style="top:124px">
    <div class="greet">Dear Mr. Rivera,</div>
    <p>Lorem ipsum dolor sit amet, consectetuer adipiscing elit, sed diam nonummy nibh euismod tincidunt ut laoreet dolore magna aliquam erat volutpat. Ut wisi enim ad minim veniam, quis nostrud exerci tation ullamcorper suscipit lobortis nisl ut aliquip ex ea commodo consequat. Duis autem vel eum iriure dolor in hendrerit in vulputate velit.</p>
    <p>Lorem ipsum dolor sit amet, consectetuer adipiscing elit, sed diam nonummy nibh euismod tincidunt ut laoreet dolore magna aliquam erat volutpat. Ut wisi enim ad minim veniam, quis nostrud exerci tation ullamcorper suscipit lobortis nisl ut aliquip ex ea commodo consequat. Duis autem vel eum iriure dolor in hendrerit.</p>
    <p>Lorem ipsum dolor sit amet, consectetuer adipiscing elit, sed diam nonummy nibh euismod tincidunt ut laoreet dolore magna aliquam erat volutpat. Ut wisi enim ad minim veniam, quis nostrud exerci tation ullamcorper suscipit lobortis nisl ut aliquip ex ea commodo consequat. Duis autem vel eum iriure dolor in hendrerit in vulputate velit esse.</p>
    <p>Lorem ipsum dolor sit amet, consectetuer adipiscing elit, sed diam nonummy nibh euismod tincidunt ut laoreet dolore magna aliquam erat volutpat. Ut wisi enim ad minim veniam, quis nostrud exerci tation ullamcorper suscipit lobortis nisl ut aliquip.</p>
    <div class="sign-off">Sincerely,</div>
    <div class="signature" role="img" aria-label="Handwritten signature of the sender"></div>
  </div>
</section>

<section class="piece env-back">
  <svg class="shape" width="431" height="60" viewBox="0 0 431 60">
    <defs><linearGradient id="envGrad" x1="0" x2="1"><stop offset="0" stop-color="#0d6cbe"/><stop offset=".6" stop-color="#17a8e4"/><stop offset="1" stop-color="#0d6cbe"/></linearGradient></defs>
    <path d="M0 13H334Q318 34 334 55H0Z" fill="url(#envGrad)"/>
    <path d="M334 13Q318 34 334 55" fill="none" stroke="#1dba94" stroke-width="1"/>
  </svg>
  <div class="env-addr">4817 NW Maple Crest Rd Unit B<br>Harborview, ST 00000</div>
  <div class="mark" style="left:330px;top:30px;width:98px">
    <span class="mark-name" style="font-size:12.5px">Bright Haven</span>
    <span class="mark-sub" style="font-size:3.6px;letter-spacing:.24em">Dental Implant Center</span>
  </div>
</section>

<section class="piece env-flap">
  <svg class="shape" width="434" height="60" viewBox="0 0 434 60">
    <defs><linearGradient id="flapGrad" x1="0" x2="1"><stop offset="0" stop-color="#17c2f0"/><stop offset="1" stop-color="#0d6cbe"/></linearGradient></defs>
    <path d="M0 0H434L424 36Q419 52 398 52H38Q18 52 12 36Z" fill="url(#flapGrad)"/>
  </svg>
  <div class="mark light" style="left:0;top:22px;width:434px">
    <span class="mark-name" style="font-size:14px">Bright Haven</span>
    <span class="mark-sub" style="font-size:4.2px">Dental Implant Center</span>
  </div>
</section>

<section class="piece folder-closed">
  <div class="folder-cover grad-band"></div>
  <div class="mark light" style="left:0;top:178px;width:264px">
    <span class="mark-name" style="font-size:30px">Bright Haven</span>
    <span class="mark-sub" style="font-size:8.5px">Dental Implant Center</span>
  </div>
  <div class="folder-inner"></div>
  <svg class="shape" width="527" height="60" viewBox="0 0 527 60">
    <defs><linearGradient id="fGrad" x1="0" x2="1"><stop offset="0" stop-color="#17a8e4"/><stop offset="1" stop-color="#0c5fae"/></linearGradient></defs>
    <path d="M264 11H448Q433 30 448 50H264Z" fill="url(#fGrad)"/>
    <path d="M448 11Q433 30 448 50" fill="none" stroke="#1dba94" stroke-width="1"/>
  </svg>
  <div class="head-contact" style="left:277px;top:16px">4817 NW Maple Crest Rd Unit B<br>Harborview, ST 00000<div class="gap"></div>&#9743; 555-318-2790<br>&#9993; info@brighthavendental.example<br>&#9679; www.brighthavendental.example</div>
  <div class="mark" style="left:444px;top:25px;width:80px">
    <span class="mark-name" style="font-size:10.5px">Bright Haven</span>
    <span class="mark-sub" style="font-size:3.2px;letter-spacing:.22em">Dental Implant Center</span>
  </div>
</section>

<section class="piece folder-open">
  <div class="open-left"></div>
  <div class="open-right"></div>
  <div class="inset-letter"></div>
  <svg class="shape" width="524" height="376" viewBox="0 0 524 376">
    <defs>
      <linearGradient id="oGrad" x1="0" x2="1"><stop offset="0" stop-color="#17a8e4"/><stop offset="1" stop-color="#0c5fae"/></linearGradient>
      <linearGradient id="pocketGrad" x1="0" y1="0" x2="1" y2="1"><stop offset="0" stop-color="#17c2f0"/><stop offset="1" stop-color="#0c5fae"/></linearGradient>
    </defs>
    <path d="M276 27H439Q425 45 439 62H276Z" fill="url(#oGrad)"/>
    <path d="M439 27Q425 45 439 62" fill="none" stroke="#1dba94" stroke-width="1"/>
    <path d="M0 241H235Q243 241 244 249L262 376H0Z" fill="url(#pocketGrad)"/>
    <path d="M277 240H524V376H261L276 248Q277 240 283 240Z" fill="url(#pocketGrad)"/>
  </svg>
  <div class="head-contact" style="left:287px;top:31px;font-size:3.8px">4817 NW Maple Crest Rd Unit B<br>Harborview, ST 00000<div class="gap" style="height:3px"></div>&#9743; 555-318-2790<br>&#9993; info@brighthavendental.example<br>&#9679; www.brighthavendental.example</div>
  <div class="mark" style="left:437px;top:39px;width:84px">
    <span class="mark-name" style="font-size:9.5px">Bright Haven</span>
    <span class="mark-sub" style="font-size:3px;letter-spacing:.2em">Dental Implant Center</span>
  </div>
  <div class="letter-body" style="left:296px;right:12px;top:118px;font-size:3.8px">
    <div class="greet" style="font-size:5.4px;margin-bottom:10px">Dear Mr. Rivera,</div>
    <p>Lorem ipsum dolor sit amet, consectetuer adipiscing elit, sed diam nonummy nibh euismod tincidunt ut laoreet dolore magna aliquam erat volutpat. Ut wisi enim ad minim veniam, quis nostrud exerci tation ullamcorper suscipit lobortis nisl ut aliquip ex ea commodo consequat.</p>
    <p>Lorem ipsum dolor sit amet, consectetuer adipiscing elit, sed diam nonummy nibh euismod tincidunt ut laoreet dolore magna aliquam erat volutpat. Ut wisi enim ad minim veniam, quis nostrud exerci tation ullamcorper suscipit lobortis nisl.</p>
    <p>Lorem ipsum dolor sit amet, consectetuer adipiscing elit, sed diam nonummy nibh euismod tincidunt ut laoreet dolore magna aliquam erat volutpat. Ut wisi enim ad minim veniam, quis nostrud exerci tation ullamcorper suscipit lobortis nisl ut aliquip ex ea.</p>
    <p>Lorem ipsum dolor sit amet, consectetuer adipiscing elit, sed diam nonummy nibh euismod tincidunt ut laoreet dolore magna aliquam erat volutpat. Ut wisi enim ad minim veniam.</p>
    <div class="sign-off" style="font-size:3.4px;margin-top:6px">Sincerely,</div>
  </div>
</section>

</body>
</html>
```